Business Card - high end, modern health care

Hey designers!

We need a double sided business card for the boutique, cutting edge physical therapy rehabilitation centre in Sydney's Northern Beaches.

With the most qualified physios in the area The Harbourview Motion Clinic does what other physiotherapy practices do not, we take our time with our patients giving them longer appointments, better physios and therefor faster results!

We guarantee that the service people receive at THMC will be unparalleled.

Hence we need a business card to reflect our modern, boutique, high end service. The final design needs to reflect that we are in a class of our own yet with the feel of beachside retreat.

Below I have attached our logo in both blue on white and white on blue. The exact colour is;
and the font that we have used in our logo is Tex Gyre Aventador.

I like the idea of the blue as the main colour as it is more eye catching and our signage onto the main road will be in this blue and in the interest of consistency across marketing the blue needs to be a part of the design. However I would appreciate a few designs onto a wooden background as this is a visual theme within the fitout of the practice.

The design needs to be of standard size (91x55mm).

Target Market(s)

We target people who have an end outcome in mind and those who have had poor experiences with other providers and ensure that everyone gets the care that they deserve with a premium service that is tailored to the individuals circumstances. As a premium service, the target market is highly educated, business and tech savvy with the additional target market of elderly people who have self funded their retirement and see value in paying for the best ongoing rehabilitation to maintain independence.

Industry/Entity Type

Physical Therapy

Contact Information for Business Card

Name, designation( Titled Musculoskeletal Physiotherapist... there will also be those in the company that have multiple designations ie 5 or 6 words long), phone number, email, facebook, instagram, address

Font styles to use
Sans Serif

Colors

Designer to choose colors to be used in the design.

Requirements
Must have
• Front - The logo as large as possible, blue or wooden theme, and all of the important details.
• Back - A blank space/lines on which to write appointment times (no "Appointment, date, time" etc.)
Nice to have
• facebook url
• logos for facebook and instagram
• Mini logos for the phone and email?

```html
<!DOCTYPE html>
<html lang="en">
<head>
<meta charset="utf-8">
<title>The Harbourview Motion Clinic — Business Card</title>
<link rel="stylesheet" href="https://fonts.googleapis.com/css2?family=Montserrat:wght@500;600;700&family=Source+Sans+3:wght@400&display=swap">
<style>
  :root {
    --backdrop: #2b2b2b;
    --brand-blue: #0553a8;
    --card-light: #efefef;
    --card-white: #ffffff;
    --ink-grey: #555555;
    --rule-grey: #6a6a6a;
    --ghost-blue: #edf1f7;
  }
  * { margin: 0; padding: 0; box-sizing: border-box; }
  html, body { width: 1200px; height: 960px; overflow: hidden; }
  body { background: var(--backdrop); position: relative; font-family: "Montserrat", sans-serif; }

  .card {
    position: absolute;
    width: 600px;
    height: 342px;
    border-radius: 18px;
    overflow: hidden;
  }
  .card-front { left: 322px; top: 108px; background: var(--brand-blue); }
  .card-back { left: 320px; top: 493px; background: var(--card-white); font-family: "Source Sans 3", sans-serif; }

  .front-shape { position: absolute; inset: 0; }

  .brand-block {
    position: absolute;
    left: 40px;
    top: 74px;
    width: 220px;
    text-align: center;
    color: var(--brand-blue);
  }
  .brand-disc {
    width: 140px; height: 140px;
    border-radius: 50%;
    background: var(--brand-blue);
    margin: 0 auto 18px;
  }
  .brand-name {
    font-weight: 700;
    font-size: 15px;
    line-height: 1.2;
    letter-spacing: 0.5px;
    text-transform: uppercase;
  }

  .contact-block {
    position: absolute;
    right: 24px;
    top: 74px;
    color: #fff;
    text-align: right;
  }
  .person-name { font-weight: 700; font-size: 20px; letter-spacing: 0.3px; line-height: 24px; }
  .person-role { font-weight: 700; font-size: 13.5px; letter-spacing: 0.4px; line-height: 18px; }
  .contact-list { list-style: none; margin-top: 9px; }
  .contact-item {
    display: flex; justify-content: flex-end; align-items: center;
    gap: 8px;
    font-weight: 500; font-size: 14px; line-height: 19px;
    white-space: nowrap;
  }
  .contact-icon { width: 13px; height: 13px; flex: none; }
  .address { margin-top: 10px; font-weight: 500; font-size: 14px; line-height: 19px; white-space: nowrap; }

  .ghost-mark { position: absolute; left: 150px; top: 30px; width: 300px; height: 300px; }

  .write-row {
    position: absolute;
    left: 32px; right: 41px;
    display: flex; align-items: flex-end; gap: 4px;
    color: var(--ink-grey);
    font-size: 16px;
  }
  .write-line { flex: 1; border-bottom: 1px solid var(--rule-grey); margin-bottom: 5px; }
  .write-line.short { flex: 0 0 114px; }
  .row-name { top: 40px; }
  .row-date { top: 83px; }
  .row-date .label-time { margin-left: 4px; }
  .row-date .label-ampm { margin-left: 4px; }

  .blank-rule {
    position: absolute;
    left: 35px; right: 41px;
    border-top: 1px solid var(--rule-grey);
  }
</style>
</head>
<body>

<section class="card card-front" aria-label="Card front">
  <svg class="front-shape" viewBox="0 0 600 342" aria-hidden="true">
    <path d="M0,0 H268 C320,50 345,170 300,260 C260,315 190,340 118,342 H0 Z" fill="var(--card-light)"/>
    <path d="M336,130 C346,220 318,292 252,342" fill="none" stroke="var(--card-light)" stroke-width="4"/>
  </svg>

  <div class="brand-block">
    <div class="brand-disc"></div>
    <p class="brand-name">The Harbourview<br>Motion Clinic</p>
  </div>

  <div class="contact-block">
    <h1 class="person-name">DANIEL REEVES</h1>
    <p class="person-role">CEO/FOUNDER</p>
    <ul class="contact-list">
      <li class="contact-item">612 408 7731
        <svg class="contact-icon" viewBox="0 0 16 16" aria-hidden="true"><path fill="#fff" d="M3.5 1l2.5 3-1.5 2c.9 2 2.5 3.6 4.5 4.5l2-1.5 3 2.5-1.5 2.5C7 14 2 9 1 2.5z"/></svg>
      </li>
      <li class="contact-item">dan@hvmotion.com
        <svg class="contact-icon" viewBox="0 0 16 16" aria-hidden="true"><rect x="1" y="3" width="14" height="10" fill="#fff"/><path d="M1 3l7 6 7-6" fill="none" stroke="var(--brand-blue)" stroke-width="1.4"/></svg>
      </li>
      <li class="contact-item">www.hvmotion.com
        <svg class="contact-icon" viewBox="0 0 16 16" aria-hidden="true"><circle cx="8" cy="8" r="7" fill="#fff"/><path d="M1 8h14M8 1c-3 3-3 11 0 14M8 1c3 3 3 11 0 14" fill="none" stroke="var(--brand-blue)" stroke-width="1"/></svg>
      </li>
      <li class="contact-item">/hvmotionclinic
        <svg class="contact-icon" viewBox="0 0 16 16" aria-hidden="true"><rect x="1" y="1" width="14" height="14" rx="2" fill="#fff"/></svg>
      </li>
      <li class="contact-item">@hvmotion
        <svg class="contact-icon" viewBox="0 0 16 16" aria-hidden="true"><rect x="1" y="1" width="14" height="14" rx="2" fill="#fff"/></svg>
      </li>
    </ul>
    <p class="address">14 Seacliff Parade<br>Manly, NSW 2095</p>
  </div>
</section>

<section class="card card-back" aria-label="Card back">
  <svg class="ghost-mark" viewBox="0 0 300 300" aria-hidden="true">
    <circle cx="150" cy="150" r="140" fill="none" stroke="var(--ghost-blue)" stroke-width="14"/>
    <text x="150" y="165" text-anchor="middle" font-family="Montserrat, sans-serif" font-weight="700" font-size="44" fill="var(--ghost-blue)">THMC</text>
  </svg>

  <div class="write-row row-name"><span>Name</span><span class="write-line"></span></div>
  <div class="write-row row-date">
    <span>Date</span><span class="write-line"></span>
    <span class="label-time">Time</span><span class="write-line short"></span>
    <span class="label-ampm">am/pm</span>
  </div>

  <div class="blank-rule" style="top:139px"></div>
  <div class="blank-rule" style="top:179px"></div>
  <div class="blank-rule" style="top:219px"></div>
  <div class="blank-rule" style="top:259px"></div>
  <div class="blank-rule" style="top:299px"></div>
</section>

</body>
</html>
```